Realtor branding business card

modern, simple and self branding. Broker office logo needs to be used but not emphasized. Looking to brand myself

Target Market(s)

buyers, sellers and investors

Industry/Entity Type

Realtor

Contact Information for Business Card

Sample of my current business card on file

Requirements
Must have
• my website - tobiasmerrowkl.com
• Realtor logo
• Fair housing logo
Nice to have
• Colors from office logo but not a must
Should not have
• Do not want headshot

```html
<!DOCTYPE html>
<html lang="en">
<head>
<meta charset="utf-8">
<title>Tobias Merrow – Business Card</title>
<link href="https://fonts.googleapis.com/css2?family=Montserrat:wght@400;500;700;800&display=swap" rel="stylesheet">
<style>
  :root {
    --stage: #2b2b2d;
    --navy: #25236e;
    --card-back: #2e2a7c;
    --card-back-deep: #241f66;
    --accent-red: #d8272d;
    --paper: #ffffff;
    --ink-gray: #5a5a5f;
    --badge-fill: #e6e6ec;
    --badge-line: #9a9aa8;
  }
  * { box-sizing: border-box; margin: 0; padding: 0; }
  html, body {
    width: 1200px; height: 780px; overflow: hidden;
    background: var(--stage);
    font-family: "Montserrat", Arial, sans-serif;
  }
  .stage {
    width: 1200px; height: 780px;
    display: flex; align-items: center; justify-content: center; gap: 40px;
  }
  .card {
    width: 560px; height: 320px;
    position: relative;
  }
  .card--back {
    background: var(--card-back);
    display: flex; align-items: center; justify-content: center;
  }
  .card--back .brand-name {
    color: var(--card-back-deep);
    font-size: 40px;
  }
  .card--front {
    background: var(--paper);
    display: flex; align-items: center;
  }
  .brand {
    display: flex; align-items: center; gap: 10px;
  }
  .brand-mark {
    width: 14px; height: 14px; background: var(--accent-red); flex: none;
  }
  .brand-name {
    font-weight: 800; color: var(--navy); line-height: 1.05;
    letter-spacing: -0.3px;
  }
  .card--front .brand {
    width: 285px; justify-content: center; padding-left: 20px;
  }
  .card--front .brand-name { font-size: 27px; }
  .divider {
    width: 2px; height: 150px; background: var(--accent-red); flex: none;
  }
  .contact {
    padding-left: 20px; color: var(--ink-gray);
  }
  .contact-name {
    color: var(--navy); font-weight: 700; font-size: 17px; letter-spacing: 0.3px;
  }
  .contact-role { font-size: 12px; margin: 2px 0 10px; }
  .contact-list { list-style: none; font-size: 12.5px; line-height: 1.45; }
  .contact-list li { display: flex; align-items: center; gap: 8px; }
  .contact-list svg { width: 11px; height: 11px; flex: none; }
  .contact-address { font-size: 12.5px; line-height: 1.4; margin-top: 10px; padding-left: 19px; }
  .badges {
    position: absolute; right: 24px; bottom: 20px;
    display: flex; gap: 10px;
  }
  .badge {
    width: 28px; height: 28px;
    background: var(--badge-fill);
    border: 1px solid var(--badge-line);
  }
</style>
</head>
<body>
<main class="stage">
  <section class="card card--back" aria-label="Card back">
    <div class="brand">
      <span class="brand-name">Brightway Realty Group</span>
    </div>
  </section>

  <section class="card card--front" aria-label="Card front">
    <div class="brand">
      <span class="brand-mark"></span>
      <span class="brand-name">Brightway<br>Realty Group</span>
    </div>
    <div class="divider"></div>
    <div class="contact">
      <h1 class="contact-name">TOBIAS MERROW</h1>
      <p class="contact-role">Realtor</p>
      <ul class="contact-list">
        <li>
          <svg viewBox="0 0 12 12" aria-hidden="true"><rect x="3" y="0.8" width="6" height="10.4" rx="1" fill="none" stroke="#25236e" stroke-width="1.2"/><circle cx="6" cy="9.3" r="0.6" fill="#25236e"/></svg>
          407. 555. 0148
        </li>
        <li>
          <svg viewBox="0 0 12 12" aria-hidden="true"><path d="M2.5 1 L4.5 1 L5.3 3.6 L4 4.6 C4.7 6 5.9 7.3 7.4 8 L8.4 6.7 L11 7.5 L11 9.5 C11 10.3 10.3 11 9.5 11 C5.4 10.6 1.4 6.6 1 2.5 C1 1.7 1.7 1 2.5 1 Z" fill="#25236e"/></svg>
          407. 555. 0190
        </li>
        <li>
          <svg viewBox="0 0 12 12" aria-hidden="true"><rect x="0.8" y="2.3" width="10.4" height="7.4" fill="none" stroke="#25236e" stroke-width="1.2"/><path d="M1 2.6 L6 6.5 L11 2.6" fill="none" stroke="#25236e" stroke-width="1.2"/></svg>
          info@tobiasmerrowkl.com
        </li>
        <li>
          <svg viewBox="0 0 12 12" aria-hidden="true"><circle cx="6" cy="6" r="5" fill="none" stroke="#25236e" stroke-width="1.1"/><ellipse cx="6" cy="6" rx="2.2" ry="5" fill="none" stroke="#25236e" stroke-width="1"/><path d="M1 6 H11 M2 3.5 H10 M2 8.5 H10" stroke="#25236e" stroke-width="0.9"/></svg>
          www.tobiasmerrowkl.com
        </li>
      </ul>
      <p class="contact-address">418 Linden Park Drive<br>Maple Springs, FL 32799</p>
    </div>
    <div class="badges">
      <div class="badge" role="img" aria-label="Realtor membership badge placeholder"></div>
      <div class="badge" role="img" aria-label="Equal housing badge placeholder"></div>
    </div>
  </section>
</main>
</body>
</html>
```